KRWB new business card design

We need a business card design for our established business which is Australia wide however based in Melbourne. We are a young team of Financial Planners who specialize in Insurance and Basic super advice for people like us.

We are people who help our clients get things done in a timely and cost effective manner whilst having a good time and a laugh along the way.

We would like this to have a consistent feel with our new e-brochure which i have attached from a color and font perspective.

Industry/Entity Type

Business

Requirements
Must have
• We do not need specific address details rather just the states we are in:

VIC/NSW/QLD/TAS
Nice to have
• Curved edge to mate the brochure

```html
<!DOCTYPE html>
<html lang="en">
<head>
<meta charset="utf-8">
<title>KRWB Advisory – Business Card</title>
<link href="https://fonts.googleapis.com/css2?family=Arimo:ital,wght@0,400;0,700;1,700&family=PT+Sans&display=swap" rel="stylesheet">
<style>
  :root {
    --backdrop: #7a5636;
    --label: #1e1208;
    --card-dark: #0c0c0c;
    --card-light: #ffffff;
    --green: #7dc242;
    --green-deep: #62b74a;
    --band: #6cbf4b;
    --text-grey: #6a6a6a;
    --text-dark: #333333;
    --white: #ffffff;
    --faint: #eef4ec;
  }
  * { box-sizing: border-box; margin: 0; padding: 0; }
  html, body { width: 1200px; height: 788px; overflow: hidden; }
  body {
    position: relative;
    background: var(--backdrop);
    font-family: "Arimo", Arial, sans-serif;
  }
  .view-label {
    position: absolute;
    width: 200px;
    text-align: center;
    font-family: "PT Sans", sans-serif;
    font-size: 22px;
    color: var(--label);
  }
  .card {
    position: absolute;
    width: 525px;
    height: 300px;
    border-radius: 20px;
    overflow: hidden;
    box-shadow: 0 4px 10px rgba(0,0,0,.35);
  }
  .card--dark { background: radial-gradient(circle at 45% 45%, #3a3a3a 0%, #111 55%, var(--card-dark) 100%); }
  .card--light { background: var(--card-light); }
  .card--mesh { background: radial-gradient(circle at 30% 40%, #2c2c2c 0%, #151515 60%, #0a0a0a 100%); }

  .abs { position: absolute; }

  /* Front */
  .accent-bar { left: 0; top: 124px; width: 10px; height: 54px; background: var(--green-deep); }
  .adviser { left: 20px; top: 124px; color: var(--green); font-weight: 700; }
  .adviser__name { font-size: 17px; line-height: 21px; }
  .adviser__role { font-size: 13px; line-height: 16px; }
  .contacts { left: 26px; top: 208px; color: var(--white); font-size: 13.5px; line-height: 17.5px; list-style: none; }
  .contacts li { display: flex; align-items: center; gap: 5px; }
  .contacts svg { width: 10px; height: 10px; fill: var(--white); }
  .brand { display: flex; align-items: center; gap: 8px; font-weight: 700; white-space: nowrap; }
  .brand__mark { width: 14px; height: 14px; background: var(--green-deep); flex: none; }
  .front-brand { right: 42px; top: 180px; font-size: 25px; color: var(--white); }
  .front-meta { right: 42px; top: 240px; text-align: right; color: var(--white); font-size: 13px; line-height: 21px; }

  /* Services */
  .services-title { font-style: italic; font-weight: 700; font-size: 18px; }
  .services { list-style: none; font-weight: 700; font-size: 14px; }
  .services li { height: 34px; line-height: 18px; }
  .services li::before {
    content: ""; display: inline-block; width: 4px; height: 4px;
    background: currentColor; margin-right: 6px; vertical-align: middle;
  }

  /* Back 1 */
  .b1-brand { left: 54px; top: 208px; font-size: 21px; color: var(--text-dark); }
  .divider { left: 260px; top: 20px; width: 2px; height: 236px;
    background: linear-gradient(to bottom, transparent, #9a9a9a 50%, transparent); }
  .b1-services { left: 320px; top: 46px; color: var(--text-grey); }
  .b1-services .services { margin-top: 15px; }
  .tag-band { left: 0; bottom: 0; width: 100%; height: 39px; background: var(--band);
    color: var(--white); font-weight: 700; font-size: 14px; line-height: 39px; text-align: center; }

  /* Back 2 */
  .faint-block { left: 150px; top: 15px; width: 226px; height: 270px; background: var(--faint); border-radius: 22px; }
  .b2-services { left: 0; width: 100%; top: 46px; text-align: center; color: var(--text-dark); }
  .b2-services .services { margin-top: 16px; }
  .b2-tagline { left: 0; width: 100%; top: 268px; text-align: center; font-weight: 700; font-size: 14px; color: #444; }

  /* Back 3 */
  .b3-brand { left: 60px; top: 240px; font-size: 26px; color: var(--white); }
  .b3-services { left: 314px; top: 24px; color: var(--white); }
  .b3-services .services { margin-top: 16px; }
  .b3-tagline { left: 313px; top: 253px; color: var(--green); font-weight: 700; font-size: 14px; line-height: 18px; }
</style>
</head>
<body>

  <div class="view-label" style="left:220px; top:33px;">Front</div>
  <div class="view-label" style="left:796px; top:33px;">Back - 1</div>
  <div class="view-label" style="left:220px; top:403px;">Back - 2</div>
  <div class="view-label" style="left:796px; top:403px;">Back - 3</div>

  <!-- Front -->
  <section class="card card--dark" style="left:54px; top:74px;">
    <div class="abs accent-bar"></div>
    <div class="abs adviser">
      <div class="adviser__name">Daniel Marsh</div>
      <div class="adviser__role">ADFS, BBus, LRS©</div>
      <div class="adviser__role">Financial Adviser</div>
    </div>
    <ul class="abs contacts">
      <li><svg viewBox="0 0 10 10"><path d="M2 0l2 2-1 1.5c.6 1.3 1.6 2.3 2.9 2.9L7.4 5.4l2 2L8 9.6C4 9.6.4 6 .4 2z"/></svg>1300 555 012</li>
      <li><svg viewBox="0 0 10 10"><rect x="2" y="0" width="6" height="3"/><rect x="0" y="3.5" width="10" height="4.5" rx="1"/><rect x="2" y="7" width="6" height="3"/></svg>03 9555 0147</li>
      <li><svg viewBox="0 0 10 10"><rect x="2.5" y="0" width="5" height="10" rx="1"/></svg>0400 555 218</li>
      <li><svg viewBox="0 0 10 10"><rect x="0" y="2" width="10" height="6.5" rx="1"/></svg>daniel@krwb.com.au</li>
    </ul>
    <div class="abs brand front-brand"><span class="brand__mark"></span>KRWB Advisory</div>
    <div class="abs front-meta">
      <div>www.krwb.com.au</div>
      <div>VIC/NSW/QLD/TAS</div>
    </div>
  </section>

  <!-- Back 1 -->
  <section class="card card--light" style="left:622px; top:74px;">
    <div class="abs brand b1-brand"><span class="brand__mark"></span>KRWB Advisory</div>
    <div class="abs divider"></div>
    <div class="abs b1-services">
      <div class="services-title">Specialising in</div>
      <ul class="services">
        <li>Risk Insurance</li><li>Debt Management</li><li>Superannuation</li><li>Wealth Creation</li><li>Retirement Planning</li>
      </ul>
    </div>
    <div class="abs tag-band">SECURE FUTURE, ENHANCED LIFESTYLE</div>
  </section>

  <!-- Back 2 -->
  <section class="card card--light" style="left:54px; top:445px;">
    <div class="abs faint-block"></div>
    <div class="abs b2-services">
      <div class="services-title">Specialising in</div>
      <ul class="services">
        <li>Risk Insurance</li><li>Debt Management</li><li>Superannuation</li><li>Wealth Creation</li><li>Retirement Planning</li>
      </ul>
    </div>
    <div class="abs b2-tagline">SECURE FUTURE, ENHANCED LIFESTYLE</div>
  </section>

  <!-- Back 3 -->
  <section class="card card--mesh" style="left:622px; top:445px;">
    <div class="abs brand b3-brand"><span class="brand__mark"></span>KRWB Advisory</div>
    <div class="abs b3-services">
      <div class="services-title">Specialising in</div>
      <ul class="services">
        <li>Risk Insurance</li><li>Debt Management</li><li>Superannuation</li><li>Wealth Creation</li><li>Retirement Planning</li>
      </ul>
    </div>
    <div class="abs b3-tagline">SECURE FUTURE<br>ENHANCED LIFESTYLE</div>
  </section>

</body>
</html>
```